BRN website video quote promotion tiles

We are promoting vehicle leasing by video, which contains several quotation examples imported from the video. We must re-vamp the quotation tiles, contact boxes, and contact form. The first tile is generated from the video, so this must be a separate project. We are looking for a welcoming, professional flow and leave color choices to design with an emphasis on communication prompts, and additional prompts in the design would be welcome.

Target Market(s)

Any Customer interaction from the tile quotes, contact, call, message,

Industry/Entity Type

vehicle leasing

Coding

Coded - Design and coding required

Number of Pages Required

1 page

Colors

Designer to choose colors to be used in the design.

Requirements
Must have
• emphasis on point of contact and visual impact on quote tile excluding main one
Should not have
• changes to the quote structure as these imported from video pricing no changes to main image as this template which can addressed as separate project

```html
<!DOCTYPE html>
<html lang="en">
<head>
<meta charset="UTF-8">
<title>Contract Hire Quotes</title>
<link href="https://fonts.googleapis.com/css2?family=Open+Sans:wght@400;600;700;800&family=Noto+Sans:wght@400&family=Poppins:wght@600&display=swap" rel="stylesheet">
<style>
  :root {
    --orange: #df7f33;
    --orange-soft: #fae0cf;
    --cream: #fbf1ea;
    --white: #ffffff;
    --ink: #111111;
    --gold: #e9b23c;
    --chat-green: #7ecf6f;
    --field-text: #555555;
  }
  * { box-sizing: border-box; margin: 0; padding: 0; }
  html, body {
    width: 1163px; height: 1200px; overflow: hidden;
    background: var(--white);
    font-family: "Open Sans", sans-serif;
  }
  .canvas { position: relative; width: 1163px; height: 1200px; }

  .quote-tile {
    position: absolute; top: 110px; width: 318px; height: 375px;
    background: var(--white);
    box-shadow: 0 2px 10px rgba(0,0,0,0.16);
  }
  .quote-tile.tile-one { left: 63px; }
  .quote-tile.tile-two { left: 423px; }
  .quote-tile.tile-three { left: 791px; }
  .tile-header { position: absolute; left: 0; top: 0; width: 318px; height: 200px; }
  .price-badge {
    position: absolute; left: 113px; top: -37px; width: 92px; height: 92px;
    border-radius: 50%; background: var(--white);
    box-shadow: 0 2px 6px rgba(0,0,0,0.12);
    text-align: center; padding-top: 29px;
  }
  .price-amount { color: var(--orange); font-weight: 700; font-size: 17px; line-height: 1; }
  .price-note { color: var(--ink); font-size: 10px; font-weight: 600; margin-top: 8px; }
  .tile-title {
    position: absolute; left: 0; width: 100%; top: 70px; text-align: center;
    color: var(--white); font-weight: 800; font-size: 32px; letter-spacing: 1px;
  }
  .tile-one .tile-title { top: 66px; }
  .tile-three .tile-title { top: 80px; }
  .tile-terms {
    position: absolute; left: 0; width: 100%; text-align: center;
    font-weight: 600; font-size: 17px; color: var(--ink); text-transform: uppercase;
  }
  .terms-line-one { top: 194px; }
  .terms-line-two { top: 227px; }
  .terms-status { top: 261px; color: var(--gold); font-weight: 400; font-size: 15px; }
  .tile-actions { position: absolute; top: 303px; left: 47px; }
  .call-button {
    position: absolute; left: 0; top: 0; width: 162px; height: 44px;
    border-radius: 22px; background: var(--orange); color: var(--white);
    font-weight: 700; font-size: 15px; display: flex; align-items: center; justify-content: center; gap: 8px;
  }
  .chat-button {
    position: absolute; left: 179px; top: -3px; width: 46px; height: 46px;
    border-radius: 50%; background: var(--chat-green); color: var(--white);
    font-weight: 700; font-size: 12px; display: flex; align-items: center; justify-content: center;
  }

  .contact-panel {
    position: absolute; left: 95px; top: 600px; width: 982px; height: 524px;
    background: var(--cream);
  }
  .contact-title {
    position: absolute; left: 0; width: 100%; top: 70px; text-align: center;
    font-weight: 800; font-size: 31px; color: var(--ink);
  }
  .form-field {
    position: absolute; background: var(--white); border-radius: 6px;
    box-shadow: 0 5px 12px rgba(120,90,70,0.16);
    font-family: "Noto Sans", sans-serif; font-size: 14px; color: var(--field-text);
    padding: 18px 17px;
  }
  .field-name { left: 71px; top: 152px; width: 402px; height: 48px; padding-top: 14px; }
  .field-email { left: 485px; top: 152px; width: 402px; height: 48px; padding-top: 14px; }
  .field-phone { left: 71px; top: 214px; width: 814px; height: 48px; padding-top: 14px; }
  .field-message { left: 71px; top: 274px; width: 818px; height: 85px; padding-top: 15px; }
  .submit-button {
    position: absolute; left: 411px; top: 381px; width: 134px; height: 50px;
    background: var(--orange); color: var(--white); border-radius: 2px;
    box-shadow: 0 6px 12px rgba(120,80,50,0.2);
    font-family: "Poppins", sans-serif; font-weight: 600; font-size: 16px;
    display: flex; align-items: center; justify-content: center;
  }
</style>
</head>
<body>
<div class="canvas">

  <section class="quote-tile tile-one">
    <svg class="tile-header" viewBox="0 0 318 200"><polygon points="0,0 318,0 318,106 157,167 0,106" fill="var(--orange)"/></svg>
    <div class="price-badge"><div class="price-amount">£247.33</div><div class="price-note">PLUS VAT</div></div>
    <h2 class="tile-title">CONTRACT HIRE</h2>
    <p class="tile-terms terms-line-one">3 Years, 9+35, 10K Miles</p>
    <p class="tile-terms terms-line-two">Annually</p>
    <p class="tile-terms terms-status">Not Maintained</p>
    <div class="tile-actions">
      <div class="call-button"><svg width="14" height="14" viewBox="0 0 24 24"><path fill="#fff" d="M6.6 10.8a15.2 15.2 0 0 0 6.6 6.6l2.2-2.2c.3-.3.7-.4 1-.2 1.1.4 2.3.6 3.6.6.6 0 1 .4 1 1V20c0 .6-.4 1-1 1A17 17 0 0 1 3 4c0-.6.4-1 1-1h3.5c.6 0 1 .4 1 1 0 1.3.2 2.5.6 3.6.1.3 0 .7-.2 1z"/></svg>CONTACT US</div>
      <div class="chat-button">Chat</div>
    </div>
  </section>

  <section class="quote-tile tile-two">
    <svg class="tile-header" viewBox="0 0 318 200">
      <path d="M0 0H318V180C290 158 265 146 235 148C190 150 140 178 90 186C55 192 25 188 0 184Z" fill="var(--orange-soft)"/>
      <path d="M0 0H318V162C290 140 265 128 235 130C190 132 140 160 90 168C55 174 25 170 0 166Z" fill="var(--orange)"/>
    </svg>
    <div class="price-badge"><div class="price-amount">£247.33</div><div class="price-note">PLUS VAT</div></div>
    <h2 class="tile-title">CONTRACT HIRE</h2>
    <p class="tile-terms terms-line-one">3 Years, 9+35, 10K Miles</p>
    <p class="tile-terms terms-line-two">Annually</p>
    <p class="tile-terms terms-status">Not Maintained</p>
    <div class="tile-actions">
      <div class="call-button"><svg width="14" height="14" viewBox="0 0 24 24"><path fill="#fff" d="M6.6 10.8a15.2 15.2 0 0 0 6.6 6.6l2.2-2.2c.3-.3.7-.4 1-.2 1.1.4 2.3.6 3.6.6.6 0 1 .4 1 1V20c0 .6-.4 1-1 1A17 17 0 0 1 3 4c0-.6.4-1 1-1h3.5c.6 0 1 .4 1 1 0 1.3.2 2.5.6 3.6.1.3 0 .7-.2 1z"/></svg>CONTACT US</div>
      <div class="chat-button">Chat</div>
    </div>
  </section>

  <section class="quote-tile tile-three">
    <svg class="tile-header" viewBox="0 0 318 200"><path d="M0 0H318V129Q159 205 0 129Z" fill="var(--orange)"/></svg>
    <div class="price-badge"><div class="price-amount">£247.33</div><div class="price-note">PLUS VAT</div></div>
    <h2 class="tile-title">CONTRACT HIRE</h2>
    <p class="tile-terms terms-line-one">3 Years, 9+35, 10K Miles</p>
    <p class="tile-terms terms-line-two">Annually</p>
    <p class="tile-terms terms-status">Not Maintained</p>
    <div class="tile-actions">
      <div class="call-button"><svg width="14" height="14" viewBox="0 0 24 24"><path fill="#fff" d="M6.6 10.8a15.2 15.2 0 0 0 6.6 6.6l2.2-2.2c.3-.3.7-.4 1-.2 1.1.4 2.3.6 3.6.6.6 0 1 .4 1 1V20c0 .6-.4 1-1 1A17 17 0 0 1 3 4c0-.6.4-1 1-1h3.5c.6 0 1 .4 1 1 0 1.3.2 2.5.6 3.6.1.3 0 .7-.2 1z"/></svg>CONTACT US</div>
      <div class="chat-button">Chat</div>
    </div>
  </section>

  <section class="contact-panel">
    <h2 class="contact-title">CONTACT US</h2>
    <div class="form-field field-name">Name</div>
    <div class="form-field field-email">Email</div>
    <div class="form-field field-phone">Phone Number</div>
    <div class="form-field field-message">Message</div>
    <div class="submit-button">Submit</div>
  </section>

</div>
</body>
</html>
```